KO!REELS WEBSITE

I need to get the design for the website of my company, which is a production company based in Los Angeles called KO! REELS. The company works as a liason between Russian speaking and English speaking film communities, providing the spectrum of production services in Eastern Europe and United States of America.
Has to have the following links:
About
Locations
Works
I'd like to see the designs on the white background using the blue and red colors.
Please try to use the font of an old typewriter if you can. You can also get some ideas after looking at the logo, which you need to intergrate into the webdesign anyway.
Thank you very much and I wish you some inspiration!
Updates

I'd like to extend the project till July the 10th, please send more submissions

Reason: I want to give more time to make changes to my comments

Target Market(s)

Production studios from different countries, Directors, Producers, Clients

Industry/Entity Type

It Company

Font styles to use
Sans Serif
Other font styles liked:
• typewriter

Requirements
Must have
• Visible logo design intergrated into graphics

```html
<!DOCTYPE html>
<html lang="en">
<head>
<meta charset="utf-8">
<title>KO! REELS — Locations</title>
<link rel="stylesheet" href="https://fonts.googleapis.com/css2?family=Special+Elite&family=Cutive+Mono&display=swap">
<style>
  :root {
    --white: #ffffff;
    --black: #000000;
    --red: #c0212f;
    --blue: #1b6aa0;
    --link-blue: #1a86e0;
    --nav-ink: #333333;
    --brand-ink: #2a2a2a;
    --overlay: rgba(60, 60, 60, 0.78);
    --body-ink: #f2f2f2;
  }
  * { margin: 0; padding: 0; box-sizing: border-box; }
  html, body {
    width: 1200px;
    height: 750px;
    overflow: hidden;
    background: var(--black);
  }
  .page {
    position: relative;
    width: 1200px;
    height: 750px;
    background: var(--black);
    font-family: "Special Elite", "Courier New", monospace;
    color: var(--body-ink);
  }
  .site-header {
    position: absolute;
    left: 0; top: 0;
    width: 1200px;
    height: 145px;
    background: var(--white);
  }
  .brand {
    position: absolute;
    left: 150px;
    top: 60px;
    display: flex;
    align-items: center;
    gap: 14px;
    white-space: nowrap;
  }
  .brand-mark {
    width: 26px;
    height: 26px;
    background: var(--blue);
  }
  .brand-name {
    font-family: "Special Elite", "Courier New", monospace;
    font-size: 38px;
    line-height: 1;
    color: var(--brand-ink);
    letter-spacing: 2px;
  }
  .brand-glow {
    position: absolute;
    left: 104px;
    top: 180px;
    width: 340px;
    height: 3px;
    background: radial-gradient(ellipse at center, rgba(80,170,230,0.95) 0%, rgba(27,106,160,0.6) 40%, rgba(27,106,160,0) 75%);
  }
  .main-nav {
    position: absolute;
    top: 113px;
    left: 0;
    width: 1200px;
    height: 32px;
  }
  .main-nav a {
    position: absolute;
    top: 0;
    font-family: "Cutive Mono", "Courier New", monospace;
    font-size: 20px;
    color: var(--nav-ink);
    text-decoration: none;
    line-height: 26px;
    white-space: nowrap;
  }
  .nav-home { left: 646px; }
  .nav-about { left: 738px; }
  .nav-locations { left: 838px; }
  .nav-works { left: 983px; }
  .nav-works::after {
    content: "";
    position: absolute;
    left: 0;
    top: 27px;
    width: 60px;
    height: 5px;
    background: var(--red);
  }
  .page-title {
    position: absolute;
    left: 143px;
    top: 278px;
    font-family: "Special Elite", "Courier New", monospace;
    font-weight: normal;
    font-size: 29px;
    color: var(--blue);
    text-decoration: underline;
    text-underline-offset: 5px;
    text-decoration-thickness: 2px;
    white-space: nowrap;
  }
  .location-card {
    position: absolute;
    top: 357px;
    width: 277px;
    height: 250px;
    overflow: hidden;
  }
  .card-one { left: 134px; }
  .card-two { left: 464px; }
  .card-three { left: 793px; }
  .card-media {
    position: absolute;
    inset: 0;
  }
  .media-map {
    background: linear-gradient(135deg, #ebe6d8 0%, #f0ebd9 45%, #e9d9a0 60%, #d7e3c6 100%);
  }
  .media-photo-crew {
    background: linear-gradient(160deg, #9a9a9a 0%, #d8d8d8 30%, #1c1c1c 60%, #050505 100%);
  }
  .media-photo-sound {
    background: linear-gradient(170deg, #e6e6e6 0%, #bdbdbd 35%, #3a3a3a 62%, #0a0a0a 100%);
  }
  .card-caption {
    position: absolute;
    left: 0;
    top: 153px;
    width: 100%;
    height: 97px;
    background: var(--overlay);
  }
  .card-title {
    position: absolute;
    left: 21px;
    top: 14px;
    font-size: 12px;
    font-weight: bold;
    color: var(--link-blue);
    text-decoration: underline;
  }
  .card-text {
    position: absolute;
    left: 37px;
    top: 36px;
    width: 224px;
    font-size: 10px;
    line-height: 12px;
    text-align: left;
    color: var(--body-ink);
  }
  .site-footer {
    position: absolute;
    left: 0;
    top: 713px;
    width: 1200px;
    text-align: center;
    font-size: 12px;
    color: var(--white);
  }
</style>
</head>
<body>
<div class="page">
  <header class="site-header">
    <div class="brand">
      <span class="brand-mark"></span>
      <span class="brand-name">KO! REELS</span>
    </div>
    <nav class="main-nav">
      <a class="nav-home" href="#">Home</a>
      <a class="nav-about" href="#">About</a>
      <a class="nav-locations" href="#">Locations</a>
      <a class="nav-works" href="#">Works</a>
    </nav>
  </header>
  <div class="brand-glow"></div>

  <main>
    <h1 class="page-title">KO! Reels Locations</h1>

    <article class="location-card card-one">
      <div class="card-media media-map" role="img" aria-label="Street map of a filming location area"></div>
      <div class="card-caption">
        <a class="card-title" href="#">Title</a>
        <p class="card-text">Lorem Ipsum is simply dummy text of the printing and typesetting industry. Lorem Ipsum has been the industry's standard dummy text ever since the 1500s, when an</p>
      </div>
    </article>

    <article class="location-card card-two">
      <div class="card-media media-photo-crew" role="img" aria-label="Black and white photo of a camera operator in silhouette"></div>
      <div class="card-caption">
        <a class="card-title" href="#">Title</a>
        <p class="card-text">Lorem Ipsum is simply dummy text of the printing and typesetting industry. Lorem Ipsum has been the industry's standard dummy text ever since the 1500s, when an</p>
      </div>
    </article>

    <article class="location-card card-three">
      <div class="card-media media-photo-sound" role="img" aria-label="Black and white photo of a camera and boom microphone in silhouette"></div>
      <div class="card-caption">
        <a class="card-title" href="#">Title</a>
        <p class="card-text">Lorem Ipsum is simply dummy text of the printing and typesetting industry. Lorem Ipsum has been the industry's standard dummy text ever since the 1500s, when an</p>
      </div>
    </article>
  </main>

  <footer class="site-footer">copyright all rights reserved - 2014</footer>
</div>
</body>
</html>
```